KVM Contracting services . Building and maintenance services, optic fibre installation

Business cards and logo design.I need a logo that I can use on business cards ,workwear and on my vehicles. I would like the KVM to be the main or larger text and contracting services to be the smaller or less important text.I like monograms, modern designs and repeating patterns symbols. I am also a Gemini and my favourite number is 22 so if this can be any inspiration to help with the design. Am thinking of the using German flag colours as a his is my family’s heritage. And the other 2 main colours I wear is black and white.But any ideas are appreciated.I do not need a design that is trade specific but a design that could be used for any business.

Target Market(s)

General public

Contact Information for Business Card

KVM Contracting Services ( front of business card)

(Back of business card)
Darren Holtwick
0451907326
Maintenance services
Optic fibre and data installation

Logo Text

Logo can just be pattern or monogram or incorporate KVM . I like the gemini star sign and the number 22

Colors
ec1f27
000000
fbee3e
ffffff

Requirements
Must have
• Logo and KVM Contracting Services on the front of business card
Nice to have
• Possible use of German flag colours.
• Modern design.
• Design to be able to be used on black or white background as I want to put it on clothing

```html
<!DOCTYPE html>
<html lang="en">
<head>
<meta charset="UTF-8">
<title>KVM Contracting Services – Business Card</title>
<link href="https://fonts.googleapis.com/css2?family=Lato:wght@400;700;900&display=swap" rel="stylesheet">
<style>
  :root {
    --red: #e0202a;
    --yellow: #e7b80c;
    --black: #000000;
    --white: #ffffff;
    --ink: #1d1d1d;
    --stage: #d9d9d9;
  }
  * { margin: 0; padding: 0; box-sizing: border-box; }
  html, body { width: 1200px; height: 900px; overflow: hidden; }
  body {
    background: var(--stage);
    font-family: "Lato", sans-serif;
    display: flex;
    flex-direction: column;
    align-items: center;
    justify-content: center;
    gap: 60px;
  }
  .card {
    width: 630px;
    height: 360px;
    border-radius: 22px;
    position: relative;
    overflow: hidden;
  }

  /* Front: white */
  .card-front {
    background: linear-gradient(135deg, #ececec 0%, var(--white) 55%);
    color: var(--ink);
  }
  .person {
    position: absolute;
    left: 44px;
    top: 58px;
  }
  .person-bars {
    position: absolute;
    left: -30px;
    top: 2px;
    display: flex;
    gap: 4px;
  }
  .person-bars span { display: block; width: 12px; height: 28px; }
  .person-bars .bar-red { background: var(--red); }
  .person-bars .bar-yellow { width: 4px; background: var(--yellow); }
  .person-name {
    font-size: 27px;
    font-weight: 400;
    color: var(--red);
    letter-spacing: 1px;
    text-transform: uppercase;
    line-height: 1;
  }
  .person-role { font-size: 15px; margin-top: 6px; }
  .divider {
    position: absolute;
    left: 150px;
    right: 40px;
    top: 120px;
    height: 1.5px;
    background: var(--ink);
  }
  .contact {
    position: absolute;
    left: 44px;
    top: 150px;
    font-size: 15px;
    line-height: 1.45;
    list-style: none;
  }
  .contact-address { margin-bottom: 4px; }
  .contact li { display: flex; align-items: center; gap: 8px; }
  .contact svg { width: 13px; height: 13px; flex: none; fill: var(--red); }

  .brand {
    position: absolute;
    right: 44px;
    bottom: 48px;
    display: flex;
    align-items: center;
    gap: 12px;
  }
  .brand-square { width: 18px; height: 18px; background: var(--yellow); }
  .brand-name {
    font-size: 26px;
    font-weight: 900;
    color: var(--red);
    text-transform: uppercase;
    letter-spacing: 0.5px;
  }

  /* Back: black */
  .card-back {
    background: var(--black);
    color: var(--white);
    display: flex;
    flex-direction: column;
    align-items: center;
    justify-content: center;
    text-align: center;
  }
  .card-back .brand { position: static; margin-bottom: 28px; }
  .card-back .brand-name { font-size: 34px; }
  .service-main {
    color: var(--yellow);
    font-size: 18px;
    letter-spacing: 1.5px;
    text-transform: uppercase;
  }
  .service-sub {
    font-size: 18px;
    letter-spacing: 1.5px;
    text-transform: uppercase;
    margin-top: 4px;
  }
</style>
</head>
<body>

  <section class="card card-front">
    <div class="person">
      <div class="person-bars"><span class="bar-red"></span><span class="bar-yellow"></span></div>
      <h1 class="person-name">Darren Holtwick</h1>
      <p class="person-role">Director</p>
    </div>
    <div class="divider"></div>
    <ul class="contact">
      <li class="contact-address">318 Linden Ave,<br>Maple Grove, FL 32190, USA</li>
      <li><svg viewBox="0 0 24 24"><path d="M6.6 10.8a15 15 0 0 0 6.6 6.6l2.2-2.2c.3-.3.7-.4 1-.2 1.1.4 2.3.6 3.6.6.6 0 1 .4 1 1V20c0 .6-.4 1-1 1A17 17 0 0 1 3 4c0-.6.4-1 1-1h3.5c.6 0 1 .4 1 1 0 1.3.2 2.5.6 3.6.1.3 0 .7-.2 1z"/></svg>0451907326</li>
      <li><svg viewBox="0 0 24 24"><path d="M2 5h20v14H2zm2 2v.5l8 5 8-5V7zm0 2.8V17h16V9.8l-8 5z"/></svg>KVM@kvmcontracting.com</li>
      <li><svg viewBox="0 0 24 24"><path d="M12 2a10 10 0 1 0 0 20 10 10 0 0 0 0-20zm0 2c.9 1.2 1.7 2.7 2.1 4.5H9.9C10.3 6.7 11.1 5.2 12 4zM4.3 14a8 8 0 0 1 0-4h3.4a17 17 0 0 0 0 4zm.8 2h3c.3 1.3.8 2.5 1.5 3.6A8 8 0 0 1 5.1 16zm3-8h-3a8 8 0 0 1 4.5-3.6C8.9 5.5 8.4 6.7 8.1 8zM12 20c-.9-1.2-1.7-2.7-2.1-4.5h4.2c-.4 1.8-1.2 3.3-2.1 4.5zm2.3-6H9.7a15 15 0 0 1 0-4h4.6a15 15 0 0 1 0 4zm.1 5.6c.7-1.1 1.2-2.3 1.5-3.6h3a8 8 0 0 1-4.5 3.6zM16.3 14a17 17 0 0 0 0-4h3.4a8 8 0 0 1 0 4z"/></svg>www.kvmcontracting.com</li>
    </ul>
    <div class="brand">
      <span class="brand-square"></span>
      <span class="brand-name">KVM Contracting Services</span>
    </div>
  </section>

  <section class="card card-back">
    <div class="brand">
      <span class="brand-square"></span>
      <span class="brand-name">KVM Contracting Services</span>
    </div>
    <p class="service-main">Maintenance Services</p>
    <p class="service-sub">Optic Fibre and Data Installation</p>
  </section>

</body>
</html>
```